Professional Single Page Website Design for Tollbrook Advisory

Tollbrook Advisory is a new business consultancy specializing in providing expert services to small businesses, primarily in the brick-and-mortar retail and food service sectors. We offer a range of services including franchise development and launch, due diligence, and construction management.

Currently, we have a basic website set up at www.tollbrookadvisory.example, but we need a professional touch to enhance its design and functionality.

Project Requirements:
- Single Page Design: For now, we need a single page design that effectively showcases who we are, our services, and contact information.
- Future Expansion: The design should be flexible and scalable for future expansion to include additional pages like specific service offerings, about us, and a dedicated contact page.
- Design Aesthetic: We are looking for a modern yet professional design that aligns with our brand identity.
- Logo: We have a logo that we like, which was also sourced from Pixel Bazaar. The logo files are attached to this project brief.

Key Sections to Include:
- Hero Section: An engaging introduction to Tollbrook Advisory with a strong visual impact.
- About Us: A brief overview of who we are and our mission.
- Team: Section for the profiles of the two principals.
- Services: A clear and concise presentation of our services, including franchise development, due diligence, and construction management.
- Contact Information: Easy-to-find contact details, including a form for inquiries.
- Call to Action: Encouraging visitors to get in touch with us for consultations or further information.

Design Considerations:
- Ensure the design is responsive and mobile-friendly.
- Include high-quality images and icons that complement our services and industry.
- We do not need development services, this is only a design project.

```html
<!DOCTYPE html>
<html lang="en">
<head>
<meta charset="utf-8">
<title>Tollbrook Advisory</title>
<link href="https://fonts.googleapis.com/css2?family=Poppins:wght@300;400;500;600;700&display=swap" rel="stylesheet">
<style>
:root{
  --navy:#0c1a24;
  --navy-2:#12293a;
  --mint:#8fd0b0;
  --mint-dark:#6fb793;
  --mint-pale:#d5f2e6;
  --sky-pale:#dbeef7;
  --ink:#1b1f24;
  --muted:#5b6670;
  --white:#ffffff;
}
*{box-sizing:border-box;margin:0;padding:0}
html,body{width:1200px;height:3971px;overflow:hidden;background:var(--white)}
body{font-family:'Poppins',sans-serif;color:var(--ink);position:relative}
.abs{position:absolute}
.photo{position:absolute}

/* header & hero */
.hero{position:absolute;left:0;top:0;width:1200px;height:720px;overflow:hidden}
.hero-photo{position:absolute;inset:0;background:linear-gradient(120deg,#07131c 0%,#0e2a3a 35%,#1f6d8a 60%,#7ec3da 80%,#1a4a5e 100%)}
.hero-shade{position:absolute;inset:0;background:linear-gradient(90deg,rgba(6,16,24,.85) 0%,rgba(6,16,24,.45) 45%,rgba(6,16,24,0) 70%)}
.brand{position:absolute;display:flex;align-items:center;gap:10px;color:var(--white);font-weight:500;font-size:24px;line-height:1}
.brand-dot{width:44px;height:44px;border-radius:50%;border:4px solid var(--white)}
.nav{position:absolute;left:561px;top:53px;display:flex;color:var(--white);font-size:17px}
.nav a{color:inherit;text-decoration:none}
.nav .sep{margin:0 24px}
.nav-line{position:absolute;left:560px;top:116px;width:525px;height:1px;background:rgba(255,255,255,.6)}
.welcome{left:116px;top:220px;color:var(--white);font-size:18px}
.hero-title{left:114px;top:256px;font-size:50px;color:var(--white);font-weight:400;white-space:nowrap}
.hero-title b{color:var(--mint);font-weight:600}
.hero-list{left:116px;top:330px;list-style:none;color:var(--white);font-size:17px}
.hero-list li{display:flex;align-items:center;gap:10px;height:43px}
.btn{position:absolute;display:flex;align-items:center;justify-content:center;gap:8px;border-radius:22px;font-weight:600;font-size:14px;text-transform:uppercase}
.btn-mint{background:var(--mint);color:var(--navy)}
.btn-navy{background:var(--navy);color:var(--white)}
.diamond-btn{position:absolute;width:54px;height:54px;background:var(--white);transform:rotate(45deg);box-shadow:0 4px 14px rgba(0,0,0,.15)}
.diamond-btn svg{transform:rotate(-45deg);position:absolute;left:17px;top:17px}

/* intro */
.eyebrow{font-size:13px;color:var(--ink);text-transform:uppercase;letter-spacing:.3px}
.h2{font-size:36px;font-weight:400;color:var(--ink);white-space:nowrap}
.h2 b{font-weight:700}
.body{font-size:14px;color:var(--muted);line-height:26px}
.city-band{left:0;top:1150px;width:1200px;height:230px;background:linear-gradient(180deg,#fff 0%,#e6e8ea 45%,#d7dadd 70%,#fff 100%)}

/* services */
.services-bg{left:0;top:1290px;width:1200px;height:820px}
.svc-title{font-size:16px;font-weight:600;color:var(--ink);text-align:right}
.svc-text{font-size:13.5px;color:var(--muted);line-height:22px;text-align:right}
.svc-icon{position:absolute;border-radius:50%;background:#eaf6f1;border:2px solid var(--mint-dark)}
.svc-num{position:absolute;width:24px;height:24px;border-radius:50%;background:var(--navy);color:var(--white);font-size:10px;display:flex;align-items:center;justify-content:center}

/* team */
.member-name{font-size:19px;font-weight:700;color:var(--ink)}
.member-role{font-size:15px;color:var(--mint-dark)}
.member-info{font-size:13.5px;color:var(--ink)}
.mini{position:absolute;width:34px;height:34px;background:var(--navy);transform:rotate(45deg);border-radius:4px}

/* contact */
.contact-bg{left:0;top:2690px;width:1200px;height:860px}
.form-card{left:446px;top:2943px;width:606px;height:413px;background:var(--white);box-shadow:0 8px 30px rgba(0,0,0,.06)}
.form-title{font-size:40px;font-weight:400;color:var(--ink);letter-spacing:.5px}
.label{font-size:15px;font-weight:500;color:var(--ink)}
.ph{font-size:12px;font-weight:500;color:#555}
.rule{height:1px;background:#9aa3aa}

/* footer */
.foot-head{font-size:19px;color:var(--mint);font-weight:500}
.foot-text{font-size:14px;color:var(--white);line-height:26px}
.foot-links{list-style:none;color:var(--white);font-size:14px}
.foot-links li{height:30.3px}
.copyright{left:0;width:1200px;top:3886px;text-align:center;color:var(--white);font-size:12.5px}
</style>
</head>
<body>

<!-- HERO -->
<section class="hero">
  <div class="hero-photo" role="img" aria-label="Upward view of glass skyscrapers against a blue sky"></div>
  <div class="hero-shade"></div>
  <div class="brand" style="left:119px;top:34px"><span class="brand-dot"></span>Tollbrook Advisory</div>
  <nav class="nav"><a>Home</a><span class="sep">|</span><a>About</a><span class="sep">|</span><a>Services</a><span class="sep">|</span><a>Team</a><span class="sep">|</span><a>Contact Us</a></nav>
  <div class="nav-line"></div>
  <p class="abs welcome">Welcome To</p>
  <h1 class="abs hero-title"><b>Tollbrook</b> Advisory</h1>
  <ul class="abs hero-list">
    <li><svg width="16" height="16" viewBox="0 0 16 16"><circle cx="8" cy="8" r="7" fill="none" stroke="#8fd0b0" stroke-width="1.5"/><path d="M5 8.2l2 2 4-4" fill="none" stroke="#8fd0b0" stroke-width="1.5"/></svg>Franchise Development and Launch</li>
    <li><svg width="16" height="16" viewBox="0 0 16 16"><circle cx="8" cy="8" r="7" fill="none" stroke="#8fd0b0" stroke-width="1.5"/><path d="M5 8.2l2 2 4-4" fill="none" stroke="#8fd0b0" stroke-width="1.5"/></svg>Due Diligence</li>
    <li><svg width="16" height="16" viewBox="0 0 16 16"><circle cx="8" cy="8" r="7" fill="none" stroke="#8fd0b0" stroke-width="1.5"/><path d="M5 8.2l2 2 4-4" fill="none" stroke="#8fd0b0" stroke-width="1.5"/></svg>Construction Management</li>
  </ul>
  <a class="btn btn-mint" style="left:116px;top:472px;width:234px;height:41px">Get in touch with us
    <svg width="14" height="14" viewBox="0 0 14 14"><circle cx="7" cy="7" r="7" fill="#0c1a24"/><path d="M6 4l3 3-3 3" fill="none" stroke="#8fd0b0" stroke-width="1.6"/></svg></a>
  <svg class="abs" style="left:0;top:580px" width="1200" height="140" viewBox="0 0 1200 140">
    <path d="M0 30 C300 110 700 110 1200 60 L1200 140 L0 140Z" fill="#8fd0b0"/>
    <path d="M0 45 C300 125 700 120 1200 80 L1200 140 L0 140Z" fill="#fff"/>
    <path d="M700 120 C900 95 1050 80 1200 70 L1200 78 C1050 90 900 110 700 125Z" fill="#0c1a24"/>
  </svg>
</section>
<div class="diamond-btn" style="left:573px;top:662px"><svg width="20" height="20" viewBox="0 0 20 20"><path d="M5 5l5 5 5-5M5 10l5 5 5-5" fill="none" stroke="#0c1a24" stroke-width="1.6"/></svg></div>

<!-- INTRO -->
<div class="abs city-band" role="img" aria-label="Soft grey cityscape of white towers"></div>
<svg class="abs" style="left:140px;top:790px" width="400" height="390" viewBox="0 0 400 390">
  <circle cx="200" cy="195" r="193" fill="#8fd0b0"/>
  <circle cx="196" cy="200" r="186" fill="#0c1a24"/>
  <circle cx="22" cy="325" r="8" fill="#6fb793"/>
</svg>
<div class="photo" role="img" aria-label="Businessman in a grey suit" style="left:150px;top:806px;width:372px;height:372px;border-radius:50%;background:linear-gradient(135deg,#3f444a 0%,#7d838a 55%,#2f3439 100%)"></div>
<div class="photo" role="img" aria-label="Modern glass office building" style="left:402px;top:1026px;width:128px;height:128px;border-radius:50%;border:6px solid #fff;background:linear-gradient(160deg,#d8eef8,#4d9fc8 60%,#1e4e6b)"></div>

<p class="abs eyebrow" style="left:625px;top:825px">Introduction</p>
<div class="abs" style="left:740px;top:834px;width:72px;height:1px;background:#c6ccd1"></div>
<h2 class="abs h2" style="left:625px;top:850px"><b>Tollbrook</b> Advisory</h2>
<p class="abs body" style="left:625px;top:906px;width:400px">Welcome to Tollbrook Advisory, your trusted partner in navigating the complexities of the real estate and small business markets.</p>
<svg class="abs" style="left:625px;top:1000px" width="40" height="40" viewBox="0 0 40 40"><circle cx="20" cy="20" r="20" fill="#0c1a24"/><circle cx="20" cy="20" r="11" fill="none" stroke="#fff" stroke-width="1.5"/><circle cx="20" cy="20" r="6" fill="none" stroke="#fff" stroke-width="1.5"/><circle cx="20" cy="20" r="1.8" fill="#fff"/></svg>
<p class="abs" style="left:679px;top:1010px;font-size:14.5px;font-weight:600;text-decoration:underline">OUR MISSION</p>
<p class="abs body" style="left:626px;top:1047px;width:400px">Lorem ipsum dolor sit amet, consectetur adipiscing elit, sed do eiusmod tempor</p>
<a class="btn btn-navy" style="left:625px;top:1122px;width:167px;height:45px">Learn more
  <svg width="14" height="14" viewBox="0 0 14 14"><circle cx="7" cy="7" r="7" fill="#fff"/><path d="M6 4l3 3-3 3" fill="none" stroke="#0c1a24" stroke-width="1.6"/></svg></a>

<!-- SERVICES -->
<svg class="abs services-bg" viewBox="0 0 1200 820" preserveAspectRatio="none">
  <defs><linearGradient id="svcg" x1="0" x2="1"><stop offset="0" stop-color="#b5ecd7"/><stop offset="1" stop-color="#dcecf6"/></linearGradient></defs>
  <path d="M0 80 C300 10 900 10 1200 80 L1200 745 C900 800 300 800 0 745Z" fill="url(#svcg)"/>
  <path d="M0 745 C300 800 900 800 1200 745 L1200 760 C900 815 300 815 0 760Z" fill="#c7ead9"/>
</svg>
<div class="abs" style="left:462px;top:1377px;width:68px;height:1px;background:#333"></div>
<p class="abs eyebrow" style="left:552px;top:1368px">Our Services</p>
<div class="abs" style="left:672px;top:1377px;width:68px;height:1px;background:#333"></div>
<h2 class="abs h2" style="left:0;width:1200px;text-align:center;top:1396px"><b>What</b> We Offer</h2>
<p class="abs body" style="left:300px;top:1467px;width:600px;text-align:center;color:#333">At Tollbrook Advisory, our Franchise Development &amp; Launch service is designed to transform your successful business into a thriving franchise.</p>

<div class="abs" style="left:149px;top:1577px;width:340px">
  <p class="svc-title">Franchise Development &amp; Launch</p>
  <p class="svc-text" style="margin-top:6px">Comprehensive franchise setup from<br>evaluation to launch for scalable<br>business growth</p>
</div>
<div class="abs" style="left:149px;top:1723px;width:304px">
  <p class="svc-title">Due Diligence</p>
  <p class="svc-text" style="margin-top:6px">Conducting thorough due diligence for<br>business and property transactions to<br>identify potential risks and liabilities.</p>
</div>
<div class="abs" style="left:149px;top:1868px;width:338px">
  <p class="svc-title">Construction Management</p>
  <p class="svc-text" style="margin-top:6px">Conducting thorough due diligence for<br>business and property transactions to<br>identify potential risks and liabilities.</p>
</div>

<div class="svc-icon" style="left:512px;top:1584px;width:92px;height:92px"></div>
<svg class="abs" style="left:532px;top:1600px" width="52" height="60" viewBox="0 0 52 60"><circle cx="26" cy="22" r="16" fill="none" stroke="#0c1a24" stroke-width="2"/><circle cx="26" cy="22" r="9" fill="none" stroke="#0c1a24" stroke-width="2"/><path d="M16 34l-6 20 8-4 4 7 4-16M36 34l6 20-8-4-4 7-4-16" fill="none" stroke="#0c1a24" stroke-width="2"/></svg>
<div class="svc-num" style="left:585px;top:1593px">01</div>
<svg class="abs" style="left:500px;top:1676px" width="30" height="34" viewBox="0 0 30 34"><path d="M14 2 C6 10 6 22 14 32" fill="none" stroke="#0c1a24" stroke-width="1.6"/><path d="M10 29l4 3 2-5" fill="none" stroke="#0c1a24" stroke-width="1.6"/></svg>

<div class="svc-icon" style="left:481px;top:1731px;width:92px;height:92px"></div>
<svg class="abs" style="left:501px;top:1751px" width="52" height="52" viewBox="0 0 52 52"><circle cx="20" cy="18" r="12" fill="none" stroke="#0c1a24" stroke-width="2"/><path d="M28 27l8 8" stroke="#0c1a24" stroke-width="3"/><rect x="30" y="36" width="4" height="10" fill="none" stroke="#0c1a24" stroke-width="1.6"/><rect x="37" y="30" width="4" height="16" fill="none" stroke="#0c1a24" stroke-width="1.6"/><rect x="44" y="24" width="4" height="22" fill="none" stroke="#0c1a24" stroke-width="1.6"/></svg>
<div class="svc-num" style="left:478px;top:1739px">02</div>
<svg class="abs" style="left:546px;top:1826px" width="30" height="34" viewBox="0 0 30 34"><path d="M12 2 C20 10 20 22 12 32" fill="none" stroke="#0c1a24" stroke-width="1.6"/><path d="M16 29l-4 3-2-5" fill="none" stroke="#0c1a24" stroke-width="1.6"/></svg>

<div class="svc-icon" style="left:515px;top:1876px;width:92px;height:92px;border-color:#0c1a24;background:#f2fbf7"></div>
<svg class="abs" style="left:535px;top:1896px" width="52" height="52" viewBox="0 0 52 52"><circle cx="26" cy="24" r="17" fill="none" stroke="#0c1a24" stroke-width="2" stroke-dasharray="6 3"/><circle cx="26" cy="19" r="6" fill="none" stroke="#0c1a24" stroke-width="2"/><path d="M16 33c2-6 18-6 20 0" fill="none" stroke="#0c1a24" stroke-width="2"/><path d="M8 44c8-4 14 2 22 0l10-6" fill="none" stroke="#0c1a24" stroke-width="2"/></svg>
<div class="svc-num" style="left:588px;top:1885px">03</div>

<svg class="abs" style="left:660px;top:1585px" width="340" height="360" viewBox="0 0 340 360" aria-hidden="true">
  <circle cx="37" cy="326" r="34" fill="#6fb793"/>
  <circle cx="298" cy="40" r="36" fill="#0c1a24"/>
</svg>
<div class="photo" role="img" aria-label="Portrait of a smiling businessman with arms crossed" style="left:642px;top:1589px;width:370px;height:370px;border-radius:50%;background:linear-gradient(160deg,#e4e2e4 0%,#d3d0d3 100%)"></div>

<!-- TEAM -->
<div class="abs" style="left:462px;top:2192px;width:68px;height:1px;background:#333"></div>
<p class="abs eyebrow" style="left:566px;top:2183px">Our Team</p>
<div class="abs" style="left:672px;top:2192px;width:68px;height:1px;background:#333"></div>
<h2 class="abs h2" style="left:0;width:1200px;text-align:center;top:2212px"><b>Leadership</b> Team</h2>

<div class="abs" style="left:0;width:359px;top:2309px;text-align:right">
  <p class="member-name">Daniel Reyes</p>
  <p class="member-role" style="margin-top:4px">Principal</p>
</div>
<p class="abs member-info" style="left:0;width:279px;text-align:right;top:2367px">+1 (555) 010 0188</p>
<p class="abs member-info" style="left:0;width:251px;text-align:right;top:2401px">info@danielreyes.example</p>
<div class="mini" style="left:292px;top:2384px"></div>
<div class="mini" style="left:256px;top:2419px"></div>
<svg class="abs" style="left:301px;top:2393px" width="16" height="16" viewBox="0 0 16 16"><path d="M4 2l3 3-2 2c1 2 2 3 4 4l2-2 3 3-2 2C7 14 2 9 2 4z" fill="#fff"/></svg>
<svg class="abs" style="left:265px;top:2429px" width="16" height="14" viewBox="0 0 16 14"><rect x="1" y="2" width="14" height="10" fill="#fff"/><path d="M1 2l7 6 7-6" fill="none" stroke="#0c1a24" stroke-width="1.2"/></svg>

<div class="abs" style="left:820px;top:2288px">
  <p class="member-name">Owen Hartley</p>
  <p class="member-role">Principal</p>
</div>
<p class="abs member-info" style="left:904px;top:2342px">+1 (555) 010 0188</p>
<p class="abs member-info" style="left:941px;top:2373px">info@danielreyes.example</p>
<div class="mini" style="left:866px;top:2359px"></div>
<div class="mini" style="left:903px;top:2394px"></div>
<svg class="abs" style="left:875px;top:2368px" width="16" height="16" viewBox="0 0 16 16"><path d="M4 2l3 3-2 2c1 2 2 3 4 4l2-2 3 3-2 2C7 14 2 9 2 4z" fill="#fff"/></svg>
<svg class="abs" style="left:912px;top:2404px" width="16" height="14" viewBox="0 0 16 14"><rect x="1" y="2" width="14" height="10" fill="#fff"/><path d="M1 2l7 6 7-6" fill="none" stroke="#0c1a24" stroke-width="1.2"/></svg>

<svg class="abs" style="left:290px;top:2310px" width="630" height="320" viewBox="0 0 630 320" aria-hidden="true">
  <rect x="55" y="50" width="210" height="210" rx="24" transform="rotate(45 160 155)" fill="#cfeadd"/>
  <rect x="365" y="45" width="210" height="210" rx="24" transform="rotate(45 470 150)" fill="#cfeadd"/>
</svg>
<div class="photo" role="img" aria-label="Portrait of Daniel Reyes" style="left:335px;top:2353px;width:230px;height:230px;border-radius:28px;transform:rotate(45deg);background:linear-gradient(135deg,#4a3a30,#8a6a52 60%,#2a2220)"></div>
<div class="photo" role="img" aria-label="Portrait of Owen Hartley" style="left:645px;top:2348px;width:230px;height:230px;border-radius:28px;transform:rotate(45deg);background:linear-gradient(135deg,#9cc0d6,#e9ecef 55%,#7c8f80)"></div>
<svg class="abs" style="left:526px;top:2380px" width="150" height="150" viewBox="0 0 150 150" aria-hidden="true">
  <rect x="28" y="28" width="94" height="94" rx="12" transform="rotate(45 75 75)" fill="#6fb793" stroke="#cfeadd" stroke-width="10"/>
  <circle cx="75" cy="75" r="26" fill="#0c1a24"/>
</svg>

<!-- CONTACT -->
<svg class="abs contact-bg" viewBox="0 0 1200 860" preserveAspectRatio="none">
  <defs><linearGradient id="ctg" x1="0" x2="1" y1="0" y2="0"><stop offset="0" stop-color="#cdebf3"/><stop offset="1" stop-color="#a9e6d1"/></linearGradient></defs>
  <path d="M0 70 C300 0 900 0 1200 70 L1200 860 L0 860Z" fill="url(#ctg)"/>
</svg>
<div class="photo" role="img" aria-label="Faint skyline silhouette" style="left:0;top:3230px;width:1200px;height:280px;background:linear-gradient(180deg,rgba(150,200,215,0) 0%,rgba(130,185,205,.55) 100%)"></div>
<div class="abs" style="left:462px;top:2786px;width:68px;height:1px;background:#333"></div>
<p class="abs eyebrow" style="left:556px;top:2777px">Contact Us</p>
<div class="abs" style="left:672px;top:2786px;width:68px;height:1px;background:#333"></div>
<h2 class="abs h2" style="left:0;width:1200px;text-align:center;top:2805px"><b>Connect</b> With Us</h2>

<div class="photo" role="img" aria-label="Glass office tower under a cloudy blue sky" style="left:126px;top:2897px;width:385px;height:388px;background:linear-gradient(160deg,#e8f2fa 0%,#7fb4d6 40%,#1f4d6e 75%,#0e2a3e 100%)"></div>
<div class="abs" style="left:750px;top:2924px;width:325px;height:309px;border:3px solid var(--navy)"></div>
<form class="abs form-card">
  <p class="abs form-title" style="left:51px;top:28px">Get &nbsp;In Touch</p>
  <p class="abs label" style="left:51px;top:93px">YOUR NAME</p>
  <p class="abs ph" style="left:51px;top:126px">Alex Morgan</p>
  <div class="abs rule" style="left:51px;top:148px;width:240px"></div>
  <p class="abs label" style="left:317px;top:93px">Email</p>
  <p class="abs ph" style="left:317px;top:126px">alex.morgan@mail.example</p>
  <div class="abs rule" style="left:317px;top:148px;width:240px"></div>
  <p class="abs label" style="left:51px;top:179px">Company</p>
  <p class="abs ph" style="left:51px;top:212px">Acme Company</p>
  <div class="abs rule" style="left:51px;top:235px;width:240px"></div>
  <p class="abs label" style="left:317px;top:179px">Phone</p>
  <p class="abs ph" style="left:317px;top:212px">+1 (555) 010 0188</p>
  <div class="abs rule" style="left:317px;top:235px;width:240px"></div>
  <p class="abs label" style="left:51px;top:270px">Message</p>
  <p class="abs ph" style="left:51px;top:303px">Hi , Do you have a moment to talk about us</p>
  <div class="abs rule" style="left:51px;top:355px;width:478px"></div>
  <svg class="abs" style="left:515px;top:319px" width="48" height="48" viewBox="0 0 48 48"><circle cx="24" cy="24" r="24" fill="#6fb793"/><path d="M14 24l20-9-7 20-4-8z" fill="#fff"/></svg>
</form>

<!-- FOOTER -->
<svg class="abs" style="left:0;top:3440px" width="1200" height="531" viewBox="0 0 1200 531">
  <path d="M0 80 C350 10 850 10 1200 80 L1200 531 L0 531Z" fill="#0c1a24"/>
  <path d="M0 60 C350 -10 850 -10 1200 60 L1200 80 C850 10 350 10 0 80Z" fill="#8fd0b0"/>
  <path d="M0 90 C300 40 500 30 600 30 L600 40 C500 40 300 55 0 100Z" fill="#0c1a24"/>
</svg>
<div class="diamond-btn" style="left:573px;top:3440px"><svg width="20" height="20" viewBox="0 0 20 20"><path d="M5 10l5-5 5 5M5 15l5-5 5 5" fill="none" stroke="#0c1a24" stroke-width="1.6"/></svg></div>

<div class="brand" style="left:174px;top:3620px"><span class="brand-dot" style="width:60px;height:60px"></span>Tollbrook Advisory</div>
<p class="abs" style="left:174px;top:3712px;color:var(--mint);font-size:16px;font-weight:500;line-height:31px">Unlock Your Business Potential<br>Today!</p>
<a class="btn btn-mint" style="left:174px;top:3790px;width:235px;height:42px;color:#fff;background:var(--mint-dark)">Get in touch with us
  <svg width="14" height="14" viewBox="0 0 14 14"><circle cx="7" cy="7" r="7" fill="#fff"/><path d="M6 4l3 3-3 3" fill="none" stroke="#6fb793" stroke-width="1.6"/></svg></a>

<p class="abs foot-head" style="left:554px;top:3604px">Contact Us</p>
<svg class="abs" style="left:554px;top:3638px" width="130" height="14" viewBox="0 0 130 14"><rect x="3" y="3" width="8" height="8" transform="rotate(45 7 7)" fill="#8fd0b0"/><path d="M12 7h90" stroke="#8fd0b0"/></svg>
<svg class="abs" style="left:550px;top:3685px" width="12" height="16" viewBox="0 0 12 16"><path d="M6 0a6 6 0 0 1 6 6c0 4-6 10-6 10S0 10 0 6a6 6 0 0 1 6-6z" fill="#fff"/><circle cx="6" cy="6" r="2" fill="#0c1a24"/></svg>
<p class="abs foot-text" style="left:581px;top:3679px;width:210px">210 Harbor View Rd Suite 40, 210 Harbor View Rd, Maplewood, CA 90000</p>
<svg class="abs" style="left:552px;top:3773px" width="14" height="14" viewBox="0 0 16 16"><path d="M4 2l3 3-2 2c1 2 2 3 4 4l2-2 3 3-2 2C7 14 2 9 2 4z" fill="#fff"/></svg>
<p class="abs foot-text" style="left:581px;top:3767px">+1 (555) 010 0188</p>
<svg class="abs" style="left:552px;top:3809px" width="16" height="13" viewBox="0 0 16 13"><rect x="0" y="0" width="16" height="13" fill="#fff"/><path d="M0 1l8 6 8-6" fill="none" stroke="#0c1a24" stroke-width="1.4"/></svg>
<p class="abs foot-text" style="left:581px;top:3802px">info@tollbrookadvisory.example</p>

<p class="abs foot-head" style="left:902px;top:3604px">Quick Links</p>
<svg class="abs" style="left:902px;top:3638px" width="130" height="14" viewBox="0 0 130 14"><rect x="3" y="3" width="8" height="8" transform="rotate(45 7 7)" fill="#8fd0b0"/><path d="M12 7h90" stroke="#8fd0b0"/></svg>
<ul class="abs foot-links" style="left:902px;top:3683px">
  <li>Home</li><li>About Us</li><li>Services</li><li>Team</li><li>Contact Us</li>
</ul>
<p class="abs copyright">Copyright@2024 - All Rights Reserved By Tollbrook Advisory</p>

</body>
</html>
```